TALVORE GROUP OF CLINICS

We need a medical & lab report file. The design should be healthcare related. Our current file design has been used for almost 10 years. We need something more fresh & up-to-date. We have attached the current file design.

Need extra days to review

```html
<!DOCTYPE html>
<html lang="en">
<head>
<meta charset="utf-8">
<title>Talvore Group – Medical Report Folder</title>
<link href="https://fonts.googleapis.com/css2?family=Poppins:wght@400;500;600;700;800&display=swap" rel="stylesheet">
<style>
  :root{
    --navy:#2b2a8f;
    --navy-deep:#23227a;
    --sky:#1fa6e0;
    --cyan:#35b8ec;
    --paper:#ffffff;
    --backdrop:#b9babd;
    --photo-a:#cfd9dd;
    --photo-b:#9fb4bc;
    --skin-a:#e9d6cc;
    --skin-b:#c9b7ae;
  }
  *{box-sizing:border-box;margin:0;padding:0}
  html,body{width:842px;height:1200px;overflow:hidden}
  body{background:var(--backdrop);font-family:"Poppins",sans-serif;position:relative}
  .spread{position:absolute;left:21px;width:800px;height:566px;display:flex;box-shadow:0 6px 18px rgba(0,0,0,.18)}
  .spread--outside{top:20px}
  .spread--inside{top:614px}
  .panel{position:relative;width:400px;height:566px;background:var(--paper);overflow:hidden}
  .panel svg.art{position:absolute;inset:0}
  .panel--inner-left{border-right:1px solid #e3e6ea}

  /* back cover contact */
  .contact{position:absolute;right:26px;top:318px;text-align:right;color:#fff;font-size:10.5px;line-height:1.45;font-weight:400}
  .contact .lines{margin-top:0}
  .contact .tel{margin-top:14px}
  .contact .tel span{display:flex;justify-content:flex-end;align-items:center;gap:6px}
  .contact svg{width:10px;height:10px}
  .contact .web{margin-top:18px;font-weight:700;font-size:12px;letter-spacing:1.5px;color:var(--cyan)}

  /* front cover */
  .brand{position:absolute;left:30px;top:300px;display:flex;align-items:center;gap:8px}
  .brand .dot{width:16px;height:16px;border-radius:50%;background:var(--navy)}
  .brand .name{font-weight:700;font-size:11px;color:var(--navy);letter-spacing:.3px}
  .title{position:absolute;left:30px;right:22px;top:360px;text-align:right}
  .title h1{font-weight:800;font-size:39px;line-height:1;color:var(--navy);letter-spacing:-.5px}
  .tagline{display:block;margin-top:4px;background:var(--sky);color:var(--navy);font-weight:700;font-size:10px;letter-spacing:5.6px;padding:2px 6px;text-align:center}
  .site{margin-top:10px;text-align:center;font-weight:700;font-size:14px;letter-spacing:2px;color:var(--navy)}
  .private{text-align:center;font-size:9px;color:var(--sky);font-weight:500;margin-top:-1px}

  /* inside faint decoration */
  .watermark{position:absolute;display:flex;align-items:center;gap:14px;opacity:.16}
  .watermark .dot{width:46px;height:46px;border-radius:50%;background:var(--navy)}
  .watermark .name{font-weight:700;font-size:34px;color:var(--navy);letter-spacing:1px}
  .watermark--left{left:50px;top:110px}
  .watermark--right{left:60px;top:180px}
</style>
</head>
<body>

<!-- Outside: back cover + front cover -->
<section class="spread spread--outside">
  <article class="panel panel--back">
    <svg class="art" viewBox="0 0 400 566" width="400" height="566">
      <defs>
        <linearGradient id="backPhoto" x1="0" y1="0" x2="1" y2="1">
          <stop offset="0" stop-color="#f4f1ee"/>
          <stop offset=".55" stop-color="var(--skin-a)"/>
          <stop offset="1" stop-color="var(--skin-b)"/>
        </linearGradient>
        <linearGradient id="hallPhoto" x1="0" y1="0" x2="0" y2="1">
          <stop offset="0" stop-color="#f2efe6"/>
          <stop offset="1" stop-color="#b9b1a2"/>
        </linearGradient>
      </defs>
      <rect width="400" height="566" fill="url(#backPhoto)" role="img" aria-label="Photo: nurse testing a patient's blood glucose with a meter"/>
      <path d="M330,0 H400 V566 H0 V470 C150,450 250,330 300,160 C312,110 322,50 330,0 Z" fill="var(--navy)"/>
      <path d="M330,0 C322,50 312,110 300,160 C250,330 150,450 0,470" fill="none" stroke="var(--cyan)" stroke-width="5"/>
      <circle cx="112" cy="455" r="98" fill="var(--paper)"/>
      <circle cx="112" cy="455" r="92" fill="url(#hallPhoto)" role="img" aria-label="Photo: clinic corridor with waiting seats"/>
    </svg>
    <div class="contact">
      <p class="lines">Suite 4, Block C<br>Orchid Park, Jalan<br>Melur 7/2, Section 7<br>47300 Petaling Jaya, Selangor</p>
      <p class="tel">
        <span>+603-7810 2244
          <svg viewBox="0 0 10 10"><path d="M2 0.5l1.6 2-1 1a5.5 5.5 0 0 0 3.4 3.4l1-1 2 1.6-1 1.8C4 9 1 6 .5 1.6z" fill="var(--cyan)"/></svg></span>
        <span>+60 12-486 1937
          <svg viewBox="0 0 10 10"><rect x="2.5" y=".5" width="5" height="9" rx="1" fill="none" stroke="var(--cyan)" stroke-width="1.2"/></svg></span>
        <span>hello@talvore.my
          <svg viewBox="0 0 10 10"><rect x=".5" y="2" width="9" height="6" fill="var(--cyan)"/><path d="M.5 2l4.5 3.5L9.5 2" fill="none" stroke="#fff" stroke-width=".8"/></svg></span>
      </p>
      <p class="web">WWW.TALVORE.MY</p>
    </div>
  </article>

  <article class="panel panel--front">
    <svg class="art" viewBox="0 0 400 566" width="400" height="566">
      <defs>
        <linearGradient id="frontPhoto" x1="0" y1="0" x2="1" y2="1">
          <stop offset="0" stop-color="var(--photo-b)"/>
          <stop offset=".5" stop-color="var(--photo-a)"/>
          <stop offset="1" stop-color="#eef2f3"/>
        </linearGradient>
      </defs>
      <path d="M0,0 H400 V268 C340,330 230,336 150,300 C80,268 30,210 0,150 Z" fill="url(#frontPhoto)" role="img" aria-label="Photo: doctor beside a patient lying in an MRI scanner"/>
      <path d="M400,268 C340,330 230,336 150,300 C140,296 130,291 122,286 C200,350 330,345 400,290 Z" fill="var(--navy)"/>
      <path d="M0,150 C20,190 45,228 70,252" fill="none" stroke="var(--navy)" stroke-width="3"/>
    </svg>
    <div class="brand"><span class="dot"></span><span class="name">TALVORE GROUP</span></div>
    <div class="title">
      <h1>MEDICAL REPORT</h1>
      <span class="tagline">YOUR HEALTHCARE PARTNER!</span>
      <p class="site">WWW.TALVORE.MY</p>
      <p class="private">Private &amp; Confidential</p>
    </div>
  </article>
</section>

<!-- Inside: pockets -->
<section class="spread spread--inside">
  <article class="panel panel--inner-left">
    <div class="watermark watermark--left"><span class="dot"></span><span class="name">TALVORE</span></div>
    <svg class="art" viewBox="0 0 400 566" width="400" height="566">
      <defs>
        <linearGradient id="pocketL" x1="0" y1="0" x2="1" y2="1">
          <stop offset="0" stop-color="var(--cyan)"/>
          <stop offset="1" stop-color="var(--sky)"/>
        </linearGradient>
      </defs>
      <path d="M0,330 L400,400 V566 H0 Z" fill="url(#pocketL)"/>
    </svg>
  </article>
  <article class="panel panel--inner-right">
    <div class="watermark watermark--right"><span class="dot"></span><span class="name">TALVORE</span></div>
    <svg class="art" viewBox="0 0 400 566" width="400" height="566">
      <defs>
        <linearGradient id="pocketR" x1="0" y1="0" x2="1" y2="1">
          <stop offset="0" stop-color="var(--cyan)"/>
          <stop offset="1" stop-color="var(--sky)"/>
        </linearGradient>
      </defs>
      <path d="M0,400 L400,330 V566 H0 Z" fill="url(#pocketR)"/>
      <path d="M0,400 L30,395 L0,430 Z" fill="#ffffff" opacity=".35"/>
    </svg>
  </article>
</section>

</body>
</html>
```